Business Card Design

We need a business card designed for our new company. Prefer a black card with white logo & writing.

Contact Information for Business Card

Ted Galloway, address: 7-4812 Fernhollow Road, Abbotsford, BC, V3K 8R2, Office Phone: 604-712-3390, Cell: 604-947-2164, Email: ted@resinworkshub.ca

Colors

Designer to choose only greyscale colors for use in the design.

```html
<!DOCTYPE html>
<html lang="en">
<head>
<meta charset="utf-8">
<title>Resinworks Hub – Business Card</title>
<link href="https://fonts.googleapis.com/css2?family=Montserrat:wght@400;500;800&display=swap" rel="stylesheet">
<style>
  :root {
    --stage: #2a2a2a;
    --card-dark: #1f1f1f;
    --mark-dark: #4a4a4a;
    --card-light: #ffffff;
    --ink: #111111;
    --ink-soft: #333333;
    --art-light: #f2f2f2;
    --art-dark: #2b2b2b;
  }
  * { margin: 0; padding: 0; box-sizing: border-box; }
  html, body { width: 1200px; height: 1200px; overflow: hidden; }
  body {
    background: var(--stage);
    font-family: "Montserrat", sans-serif;
    position: relative;
  }
  .card {
    position: absolute;
    left: 180px;
    width: 840px;
    height: 480px;
    overflow: hidden;
  }
  .card--back {
    top: 90px;
    background: var(--card-dark);
    display: flex;
    align-items: center;
    justify-content: center;
  }
  .brand-name {
    font-weight: 800;
    letter-spacing: 1px;
    line-height: 1;
    white-space: nowrap;
  }
  .card--back .brand-name {
    font-size: 64px;
    color: var(--mark-dark);
  }
  .card--front {
    top: 630px;
    background: var(--card-light);
    color: var(--ink);
  }
  .card--front .brand-name {
    position: absolute;
    left: 48px;
    top: 62px;
    font-size: 40px;
    color: var(--ink);
  }
  .holder {
    position: absolute;
    right: 72px;
    top: 58px;
    text-align: right;
  }
  .holder__name { font-weight: 800; font-size: 27px; }
  .holder__role { font-weight: 400; font-size: 17px; color: var(--ink-soft); margin-top: 8px; }
  .edge-tab {
    position: absolute;
    right: 0;
    top: 72px;
    width: 30px;
    height: 62px;
    background: var(--ink);
  }
  .contacts {
    position: absolute;
    left: 48px;
    top: 210px;
    list-style: none;
    font-size: 19px;
    font-weight: 500;
  }
  .contacts li {
    display: flex;
    align-items: center;
    gap: 16px;
    height: 34px;
  }
  .contacts svg { width: 18px; height: 18px; flex: none; }
  .address {
    position: absolute;
    left: 48px;
    top: 370px;
    font-size: 19px;
    font-weight: 500;
    line-height: 1.3;
    font-style: normal;
  }
  .scenery {
    position: absolute;
    right: 0;
    bottom: 0;
    width: 400px;
    height: 190px;
    background: linear-gradient(180deg, var(--art-light) 0%, var(--art-dark) 100%);
  }
</style>
</head>
<body>
  <section class="card card--back" aria-label="Card back">
    <span class="brand-name">RESINWORKS HUB</span>
  </section>

  <section class="card card--front" aria-label="Card front">
    <span class="brand-name">RESINWORKS HUB</span>

    <div class="holder">
      <div class="holder__name">Ted Galloway</div>
      <div class="holder__role">owner</div>
    </div>
    <div class="edge-tab"></div>

    <ul class="contacts">
      <li>
        <svg viewBox="0 0 24 24"><path fill="#111" d="M6.6 10.8a15 15 0 0 0 6.6 6.6l2.2-2.2a1 1 0 0 1 1-.25 11.4 11.4 0 0 0 3.6.57 1 1 0 0 1 1 1V20a1 1 0 0 1-1 1A17 17 0 0 1 3 4a1 1 0 0 1 1-1h3.5a1 1 0 0 1 1 1c0 1.25.2 2.45.57 3.57a1 1 0 0 1-.25 1z"/></svg>
        <span>604-712-3390</span>
      </li>
      <li>
        <svg viewBox="0 0 24 24"><rect x="6" y="2" width="12" height="20" rx="2" fill="none" stroke="#111" stroke-width="2.4"/><circle cx="12" cy="18" r="1.3" fill="#111"/></svg>
        <span>604-947-2164</span>
      </li>
      <li>
        <svg viewBox="0 0 24 24"><rect x="2" y="5" width="20" height="14" fill="#111"/><path d="M2 5l10 8 10-8" fill="none" stroke="#fff" stroke-width="1.6"/></svg>
        <span>ted@resinworkshub.ca</span>
      </li>
      <li>
        <svg viewBox="0 0 24 24"><circle cx="12" cy="12" r="10" fill="#111"/><path d="M2 12h20M12 2c3 3 3 17 0 20M12 2c-3 3-3 17 0 20" fill="none" stroke="#fff" stroke-width="1.3"/></svg>
        <span>www.resinworkshub.ca</span>
      </li>
    </ul>

    <address class="address">
      7-4812 Fernhollow Road,<br>
      Abbotsford, BC, V3K 8R2
    </address>

    <div class="scenery" role="img" aria-label="Mountain peak silhouette illustration"></div>
  </section>
</body>
</html>
```